Fastest Work at home Solution for Small Businesses

We need a web page for a product called *BrightReed*
We develop an innovative VPN Appliance (Model-Name ->Reed Alpha) that gives small business the possibility literally setup the possibility for Companies to let their employees work from home.
With our secure appliance we create safe connection between any business and the employee *working at home*
Our Products *Reed Alpha* are rolled out in minutes.
A. Employees can connect directly
B. Work from any location
C. All this without having to change the company firewall
Use case
=======
1. Go to our page
2. Select Product
3. Order
4. Connect to any Switch in the company
5. install software on employees laptop
***** INSTANT Connection ******
Target Market(s)
Businesses
Coding
Coded - Design and coding required
Number of Pages Required
3 page
Font styles to use
Look and feel
Each slider illustrates characteristics of the customer's brand and the style your logo design should communicate.

```html
<!DOCTYPE html>
<html lang="en">
<head>
<meta charset="utf-8">
<title>BrightReed – Fastest Work at home Solution for Small Businesses</title>
<link rel="stylesheet" href="https://fonts.googleapis.com/css2?family=Poppins:wght@300;400;500;600&family=Open+Sans:wght@400;600&display=swap">
<style>
:root{
  --navy:#0b1a45;
  --navy-deep:#050e33;
  --ink:#0d1b3e;
  --blue:#0a3cb0;
  --blue-2:#0f5ccc;
  --link:#1f55c5;
  --sky:#5ec8f5;
  --ring:#d5dcf3;
  --grey:#5f5c57;
  --text:#3a3a3a;
  --line:#c9ccd3;
  --white:#ffffff;
}
*{margin:0;padding:0;box-sizing:border-box}
html,body{width:1200px;height:3459px;overflow:hidden;background:var(--white)}
body{font-family:"Open Sans",Arial,sans-serif;color:var(--text)}
.page{position:relative;width:1200px;height:3459px;overflow:hidden}
h1,h2,h3{font-family:"Poppins",Arial,sans-serif;font-weight:500}

/* header */
.site-header{position:absolute;left:0;top:0;width:1200px;height:80px;background:var(--white);z-index:5}
.brand{position:absolute;left:144px;top:16px;display:flex;align-items:center;gap:12px;font-family:"Poppins",sans-serif;font-weight:600;font-size:36px;color:var(--ink)}
.brand-dot{width:30px;height:30px;border-radius:50%;background:var(--blue)}
.main-nav{position:absolute;top:30px;left:0;font-family:"Poppins",sans-serif;font-size:16px;color:var(--ink)}
.main-nav a{position:absolute;white-space:nowrap;color:inherit;text-decoration:none}
.main-nav a.active{color:var(--link)}

/* hero */
.hero{position:absolute;left:0;top:80px;width:1200px;height:540px;background:var(--grey);overflow:hidden}
.hero-photo{position:absolute;left:561px;top:0;width:639px;height:540px;background:linear-gradient(135deg,#e9e6e1 0%,#cfd6de 45%,#7f95b3 75%,#2c2f36 100%)}
.hero-title{position:absolute;left:144px;top:145px;font-size:37px;line-height:56px;color:var(--white);font-weight:400;white-space:nowrap}
.btn{display:flex;align-items:center;justify-content:center;border-radius:30px;background:linear-gradient(90deg,#0a34a6,#1556d0);color:var(--white);font-family:"Poppins",sans-serif;text-decoration:none}
.hero-btn{position:absolute;left:144px;top:324px;width:160px;height:55px;font-size:19px}
.wave{position:absolute;left:0;width:1200px;display:block}

/* welcome */
.section-title{position:absolute;left:0;width:1200px;text-align:center;font-size:43px;font-weight:600;color:var(--ink)}
.welcome-text{position:absolute;left:144px;top:773px;width:912px;text-align:center;font-size:17px;line-height:32px;color:#3d3d3d}

/* product band */
.product-band{position:absolute;left:0;top:990px;width:1200px;height:660px}
.title-sky{color:var(--sky)}
.feature{position:absolute;width:300px;text-align:center}
.feature-badge{position:absolute;left:60px;top:-17px;width:180px;height:180px;border-radius:50px;background:var(--white);transform:rotate(45deg)}
.feature-icon{position:absolute;left:96px;top:19px;width:108px;height:108px}
.feature-label{position:absolute;left:0;top:198px;width:300px;font-family:"Poppins",sans-serif;font-size:25px;line-height:38px;color:var(--white)}

/* how it works */
.step{position:absolute;width:200px;text-align:center}
.step-ring{position:absolute;left:22px;top:0;width:156px;height:156px;border-radius:50%;border:7px solid var(--ring)}
.step-arrow{position:absolute;left:167px;top:66px;width:22px;height:22px;border-radius:50%;background:var(--ring)}
.step-icon{position:absolute;left:65px;top:43px;width:70px;height:70px}
.step-label{position:absolute;left:0;top:172px;width:200px;font-family:"Poppins",sans-serif;font-size:17px;line-height:24px;color:var(--link)}
.cta-btn{position:absolute;left:464px;top:2063px;width:272px;height:55px;font-size:19px;font-weight:600}

/* reviews */
.review-card{position:absolute;top:2390px;width:297px;height:191px;background:var(--white);padding:62px 10px 0 24px;font-size:14px;line-height:27px;color:#2d2d2d;white-space:nowrap}
.review-card::after{content:"";position:absolute;left:18px;bottom:-16px;border-left:16px solid transparent;border-right:16px solid transparent;border-top:16px solid var(--white)}
.quote-mark{position:absolute;left:24px;top:18px;font-family:"Poppins",sans-serif;font-size:44px;line-height:44px;color:#9aa6bf;font-weight:600}
.reviewer{position:absolute;top:2606px;height:64px;display:flex;align-items:center;gap:8px}
.reviewer-avatar{width:64px;height:64px;border-radius:50%;background:linear-gradient(135deg,#c8b6a4,#6f5f52)}
.reviewer-name{font-family:"Poppins",sans-serif;font-size:26px;line-height:32px;color:var(--sky)}
.reviewer-city{font-size:12px;color:#5a86c8}
.slider-arrow{position:absolute;top:2515px}

/* contact */
.contact-intro{position:absolute;left:144px;top:2960px;width:440px;font-size:11.5px;line-height:21px;color:#222}
.contact-row{position:absolute;left:144px;display:flex;align-items:center;gap:12px;font-family:"Poppins",sans-serif;font-size:22px;color:var(--ink)}
.contact-icon{width:32px;height:32px;border-radius:50%;border:3px solid #dcebfb;background:#eef6fe;display:flex;align-items:center;justify-content:center}
.field{position:absolute;height:40px;border:1px solid var(--line);font-size:13px;color:#888;padding:11px 14px}
.field-message{height:80px}
.submit-btn{position:absolute;left:609px;top:3151px;width:102px;height:42px;font-size:16px;font-weight:600}

/* footer */
.footer-links{position:absolute;left:144px;top:3364px;font-size:12px;color:#8ea2cc}
.footer-links span{margin:0 8px}
.copyright{position:absolute;left:144px;top:3401px;font-size:12px;color:#8ea2cc}
.social{position:absolute;top:3376px;width:24px;height:24px;border-radius:50%;background:#6b85c0}
</style>
</head>
<body>
<div class="page">

  <header class="site-header">
    <div class="brand"><span class="brand-dot"></span>BrightReed</div>
    <nav class="main-nav">
      <a class="active" style="left:479px" href="#">Home</a>
      <a style="left:558px" href="#">About Us</a>
      <a style="left:656px" href="#">Products</a>
      <a style="left:756px" href="#">How It Works</a>
      <a style="left:882px" href="#">Reviews</a>
      <a style="left:976px" href="#">Contact Us</a>
    </nav>
  </header>

  <section class="hero">
    <div class="hero-photo" role="img" aria-label="Smiling man on the phone at a desk with a computer in a bright home office"></div>
    <h1 class="hero-title">Fastest Work at home<br>Solution for<br>Small Businesses</h1>
    <a class="btn hero-btn" href="#">READ MORE</a>
    <svg class="wave" style="top:470px" width="1200" height="70" viewBox="0 0 1200 70" preserveAspectRatio="none">
      <path d="M0 28 C150 -10 260 60 400 44 C520 30 560 0 700 8 C850 16 920 70 1060 40 C1120 28 1170 10 1200 6 L1200 70 L0 70 Z" fill="var(--white)"/>
    </svg>
  </section>

  <h2 class="section-title" style="top:703px">Welcome to BrightReed</h2>
  <p class="welcome-text">Pellentesque blandit lacus eget nunc faucibus, et tincidunt eros viverra. Phasellus consequat sagittis nisi suscipit feugiat. Cras eget leo sed nunc hendrerit ultricies eu at nisl. Praesent iaculis faucibus urna sit amet lacinia. Maecenas consequat justo enim, ac mattis massa imperdiet quis. Fusce eget neque elit. Sed augue orci, elementum in magna congue, tincidunt vulputate erat. Aliquam consectetur orci molestie.</p>

  <section class="product-band">
    <svg class="wave" style="top:0" width="1200" height="660" viewBox="0 0 1200 660" preserveAspectRatio="none">
      <defs><linearGradient id="bandBlue" x1="0" x2="1"><stop offset="0" stop-color="#0a36a8"/><stop offset="1" stop-color="#0f5ccc"/></linearGradient></defs>
      <path d="M0 2 C120 30 220 40 330 32 C450 22 520 10 600 14 C720 20 800 42 920 36 C1040 30 1120 10 1200 0 L1200 620 C1120 640 1060 650 960 640 C860 630 760 608 640 610 C500 614 440 650 300 650 C180 650 80 628 0 614 Z" fill="url(#bandBlue)"/>
    </svg>
    <h2 class="section-title title-sky" style="top:124px">Our Product</h2>

    <div class="feature" style="left:141px;top:233px">
      <div class="feature-badge"></div>
      <svg class="feature-icon" viewBox="0 0 100 100" fill="none" stroke="var(--blue)" stroke-width="3" stroke-linejoin="round">
        <path d="M40 18 h44 a4 4 0 0 1 4 4 v30 a4 4 0 0 1-4 4 h-4 v10 l-8-10"/>
        <path d="M14 32 h52 a4 4 0 0 1 4 4 v30 a4 4 0 0 1-4 4 h-34 l-12 12 v-12 h-6 a4 4 0 0 1-4-4 v-30 a4 4 0 0 1 4-4z"/>
        <path d="M22 46 h36 M22 54 h36 M22 62 h22"/>
      </svg>
      <div class="feature-label">Employees can<br>connect directly</div>
    </div>

    <div class="feature" style="left:461px;top:233px">
      <div class="feature-badge"></div>
      <svg class="feature-icon" viewBox="0 0 100 100" fill="none" stroke="var(--blue)" stroke-width="3">
        <circle cx="52" cy="54" r="34"/>
        <path d="M34 10 a12 12 0 0 1 12 12 c0 10-12 22-12 22 s-12-12-12-22 a12 12 0 0 1 12-12z" fill="var(--white)"/>
        <circle cx="34" cy="22" r="4"/>
        <path d="M66 50 a10 10 0 0 1 10 10 c0 8-10 18-10 18 s-10-10-10-18 a10 10 0 0 1 10-10z" fill="var(--white)"/>
      </svg>
      <div class="feature-label">Work from any<br>location</div>
    </div>

    <div class="feature" style="left:780px;top:233px">
      <div class="feature-badge"></div>
      <svg class="feature-icon" viewBox="0 0 100 100" fill="none" stroke="var(--blue)" stroke-width="3">
        <rect x="8" y="18" width="66" height="52"/>
        <path d="M8 31 h66 M8 44 h66 M8 57 h66 M28 18 v13 M52 18 v13 M18 31 v13 M40 31 v13 M62 31 v13 M28 44 v13 M52 44 v13 M18 57 v13 M40 57 v13"/>
        <path d="M76 52 l16 6 v10 c0 10-8 16-16 20 c-8-4-16-10-16-20 v-10z" fill="var(--white)"/>
        <path d="M69 70 l5 5 l9-10"/>
      </svg>
      <div class="feature-label">All this without having<br>to change the<br>company firewall</div>
    </div>
  </section>

  <h2 class="section-title" style="top:1727px">How It Works</h2>

  <div class="step" style="left:124px;top:1803px">
    <div class="step-ring"></div><div class="step-arrow"></div>
    <svg class="step-icon" viewBox="0 0 70 70" fill="none" stroke="var(--blue)" stroke-width="2"><rect x="6" y="10" width="58" height="50"/><path d="M6 18 h58 M12 24 h24 v12 h-24z M42 26 h16 M42 32 h16 M12 42 h14 v10 h-14z M30 42 h12 v10 h-12z M46 42 h12 v10 h-12z"/></svg>
    <div class="step-label">Go to our page</div>
  </div>
  <div class="step" style="left:312px;top:1803px">
    <div class="step-ring"></div><div class="step-arrow"></div>
    <svg class="step-icon" viewBox="0 0 70 70" fill="none" stroke="var(--blue)" stroke-width="2"><rect x="14" y="6" width="42" height="58" rx="3"/><circle cx="22" cy="18" r="3"/><circle cx="22" cy="30" r="3"/><circle cx="22" cy="42" r="3"/><circle cx="22" cy="54" r="3"/><path d="M30 18 h20 M30 30 h20 M30 42 h20 M30 54 h20"/></svg>
    <div class="step-label">Select Product</div>
  </div>
  <div class="step" style="left:500px;top:1803px">
    <div class="step-ring"></div><div class="step-arrow"></div>
    <svg class="step-icon" viewBox="0 0 70 70" fill="none" stroke="var(--blue)" stroke-width="2"><rect x="8" y="18" width="50" height="32" rx="3"/><path d="M8 26 h50"/><rect x="18" y="28" width="50" height="30" rx="3" fill="var(--white)"/><rect x="46" y="40" width="14" height="8"/></svg>
    <div class="step-label">Order</div>
  </div>
  <div class="step" style="left:688px;top:1803px">
    <div class="step-ring"></div><div class="step-arrow"></div>
    <svg class="step-icon" viewBox="0 0 70 70" fill="none" stroke="var(--blue)" stroke-width="2"><circle cx="22" cy="18" r="8"/><circle cx="22" cy="18" r="3"/><circle cx="50" cy="16" r="7"/><circle cx="50" cy="16" r="2.5"/><path d="M30 56 v-18 a3 3 0 0 1 6 0 v10 m0-4 a3 3 0 0 1 6 0 v4 m0-2 a3 3 0 0 1 6 0 v10 c0 6-4 8-8 8 h-6 c-4 0-6-4-10-8"/><path d="M8 44 v8 M12 40 v12 M56 42 v10 M60 46 v6"/></svg>
    <div class="step-label">Connect to any<br>Switch in the<br>company</div>
  </div>
  <div class="step" style="left:876px;top:1803px">
    <div class="step-ring"></div>
    <svg class="step-icon" viewBox="0 0 70 70" fill="none" stroke="var(--blue)" stroke-width="2"><rect x="14" y="18" width="42" height="28" rx="2"/><path d="M6 52 h58 l-4 4 h-50z"/></svg>
    <div class="step-label">Install software on<br>employees laptop</div>
  </div>

  <a class="btn cta-btn" href="#">INSTANT CONNECTION</a>

  <svg class="wave" style="top:2196px" width="1200" height="610" viewBox="0 0 1200 610" preserveAspectRatio="none">
    <path d="M0 14 C120 0 220 36 330 40 C440 44 500 4 600 2 C720 0 800 40 920 40 C1040 40 1120 8 1200 0 L1200 560 C1120 580 1040 596 920 592 C800 588 720 556 600 556 C480 556 420 600 300 604 C180 608 80 580 0 566 Z" fill="var(--navy)"/>
  </svg>
  <h2 class="section-title title-sky" style="top:2320px">Reviews</h2>

  <svg class="slider-arrow" style="left:54px" width="22" height="32" viewBox="0 0 22 32" fill="none" stroke="#8c96ad" stroke-width="3"><path d="M18 2 L4 16 L18 30"/></svg>
  <svg class="slider-arrow" style="left:1124px" width="22" height="32" viewBox="0 0 22 32" fill="none" stroke="#8c96ad" stroke-width="3"><path d="M4 2 L18 16 L4 30"/></svg>

  <div class="review-card" style="left:145px"><span class="quote-mark">“</span>Phasellus nisl est, condimentum vitae<br>faucibus in, sollicitudin vel metus.<br>Nunc sit amet consequat risus.<br>Curabi tur ac elit leo eleifend dui.</div>
  <div class="review-card" style="left:452px"><span class="quote-mark">“</span>Phasellus nisl est, condimentum vitae<br>faucibus in, sollicitudin vel metus.<br>Nunc sit amet consequat risus.<br>Curabi tur ac elit leo eleifend dui.</div>
  <div class="review-card" style="left:760px"><span class="quote-mark">“</span>Phasellus nisl est, condimentum vitae<br>faucibus in, sollicitudin vel metus.<br>Nunc sit amet consequat risus.<br>Curabi tur ac elit leo eleifend dui.</div>

  <div class="reviewer" style="left:145px"><div class="reviewer-avatar" role="img" aria-label="Portrait photo of reviewer"></div><div><div class="reviewer-name">Mark Dalton</div><div class="reviewer-city">Brisbane</div></div></div>
  <div class="reviewer" style="left:452px"><div class="reviewer-avatar" role="img" aria-label="Portrait photo of reviewer"></div><div><div class="reviewer-name">Clara</div><div class="reviewer-city">Sydney</div></div></div>
  <div class="reviewer" style="left:760px"><div class="reviewer-avatar" role="img" aria-label="Portrait photo of reviewer"></div><div><div class="reviewer-name">Ravi</div><div class="reviewer-city">Melbourne</div></div></div>

  <h2 class="section-title" style="top:2886px">Contact Us</h2>
  <p class="contact-intro">Maecenas vel tortor accumsan quam varius imperdiet vel eget elit. Aenean facilisis tincidunt lectus, id dictum nisi luctus eget. Vivamus efficitur ex condimentum, malesuada eros eget, feugiat nibh.</p>
  <div class="contact-row" style="top:3040px">
    <span class="contact-icon"><svg width="14" height="14" viewBox="0 0 24 24" fill="var(--blue)"><path d="M6.6 10.8a15 15 0 0 0 6.6 6.6l2.2-2.2a1 1 0 0 1 1-.25 11.4 11.4 0 0 0 3.6.57 1 1 0 0 1 1 1V20a1 1 0 0 1-1 1A17 17 0 0 1 3 4a1 1 0 0 1 1-1h3.5a1 1 0 0 1 1 1c0 1.25.2 2.45.57 3.57a1 1 0 0 1-.25 1z"/></svg></span>555 204 7781
  </div>
  <div class="contact-row" style="top:3091px">
    <span class="contact-icon"><svg width="13" height="10" viewBox="0 0 26 20" fill="var(--blue)"><path d="M0 0h26v3L13 11 0 3z M0 6l13 8 13-8v14H0z"/></svg></span>hello@brightreed.example
  </div>

  <div class="field" style="left:609px;top:2963px;width:218px">Full Name</div>
  <div class="field" style="left:835px;top:2963px;width:217px">Email Address</div>
  <div class="field" style="left:609px;top:3011px;width:218px">Phone Number</div>
  <div class="field" style="left:835px;top:3011px;width:217px">Title</div>
  <div class="field field-message" style="left:609px;top:3059px;width:443px">Message</div>
  <a class="btn submit-btn" href="#">SUBMIT</a>

  <svg class="wave" style="top:3270px" width="1200" height="189" viewBox="0 0 1200 189" preserveAspectRatio="none">
    <path d="M0 10 C120 30 220 44 340 44 C460 44 520 8 640 6 C760 4 840 42 960 42 C1060 42 1130 20 1200 6 L1200 189 L0 189 Z" fill="var(--navy-deep)"/>
  </svg>
  <div class="footer-links">Home<span>|</span>About Us<span>|</span>Products<span>|</span>How It Works<span>|</span>Reviews<span>|</span>Contact Us</div>
  <div class="copyright">Copyright © 2021 BrightReed. All rights reserved.</div>
  <span class="social" style="left:979px" aria-label="Social link"></span>
  <span class="social" style="left:1030px" aria-label="Social link"></span>

</div>
</body>
</html>
```